Wine Label Design-Hollow Creek Vineyard

Hollow Creek Vineyard is in the Barossa Valley in South Australia. The Barossa is recognized as Australia's premier wine region, producing Australia's icon wines and some " new takes on traditional".
This family owned and operated vineyard grows some exceptionally high quality fruit. Most of the fruit is sold and used for some of Australia's most iconic wines. Small quantities are retained by the owners for some wines with very limited availability. (Wines were previously sold as Brackwell Vineyards Hollow Creek ( Shiraz, Cabernet etc).

The wines will in the future be labeled simply ‘Hollow Creek Vineyard’. The label will launch this new identity for the single family single vineyard and its high quality wines which are a true expression of the vineyard and derive from the Hollow Creek common to this ancient area (800-2000 million years old).
The label should reflect
• Single vineyard, family owned
• vines in very old rock & soils
• High quality & reliability
• Edgy but true, design based thinking (Please note:blue is generally seen as an unacceptable colour for a wine label?? Don’t ask me why)

The wines will be sold mostly direct in Australia ( ie not through retail stores), with limited export to Asia, Scandinavia and Canada.
There are three quality levels and price points in the portfolio
1. Entry level premium for everyday drinking for discriminating drinkers-approx AUD20
2. Super Premium-approx AUD30
3. Limited Release ultlra premium-AUD75-90?
We envisage three variations on the label but with an obvious & common design element. This design element should be able to be used for corporate identification and promotion
The paper stock will be waterproof and self adhesive. Our preference is for designs that engage the user by appealing to both sight and touch. It is preferred that textures be added eg embossing, high build varnish etc-rather than be a facet of the stock itself.
For information on statutory label requirements refer to www.vintnerregistry-example.com . In brief
o Front label need not show any mandatory information. However we would prefer Variety, Barossa Valley, Year and alcohol to be shown on the front label
o Back label should show all mandatories and allow for a bar code
Updates

Project Deadline Extended
Reason: I've had a problem with my wireless broadband account and reception has been intermittent to say the least to the extent that I switched off at the weekend. Just going downtown now for a 'polite discussion' with my service provider.

Project Deadline Extended
Reason: I have receiver insufficient designs of quality which we would consider. Too many designs have a "cut and paste" appearance - too few exhibit an original art/design element which truly identifies the product.

Gals & Guys

most of the designs submitted lack punch and originality and are totally unmemorable.
Please-get on Searcho or whatever enter "Wine Label Designs" and do some research b4 u waste your time and mine. Formulaic cut and paste will not win the day. That's not to say that cut and paste can't work-but it must have some originality, impact and command attention. Please surprise me.

Following on from a question from a designer about who is our competition and what we are looking for I sent the following 
"I don't think I can add anything new. Read the brief and comments again and research wine labels on the web. In 30 minutes you'll get a good idea of the creative edgy designs in the industry. There are a plethora of collections. Our competition-anyone with a label. In 2010 there were over 2400 "producers" in other words 2400 producers with at least one label. In fact there are over 25000 Australian wines and then the numerous imported wines.

Target Market(s)

$20 people who budget everyday but have graduated from drinking 'entry level' wines. These people will likely fit into Cat. (b) in the $30 wine

$30 (a) will not over-compromise on some everyday discretionary expenditure.(b) might buy for special occasions

$70-$90 Professional/successful people with high disposable/discretionary income not particularly worried about recession. wine geeks.

Industry/Entity Type

Retail

Requirements
Must have
• identifiable element across range of wines

```html
<!DOCTYPE html>
<html lang="en">
<head>
<meta charset="utf-8">
<title>Hollow Creek Vineyards – Barossa Valley 2012 Bordeaux Labels</title>
<link rel="stylesheet" href="https://fonts.googleapis.com/css2?family=Open+Sans:wght@700;800&display=swap">
<style>
  :root {
    --page: #ffffff;
    --frame: #c9c9cc;
    --frame-edge: #a9a9ad;
    --wine-red: #d23b3b;
    --wine-red-light: #e27470;
    --wine-red-mid: #d9524f;
    --ink-white: #ffffff;
    --ink-grey: #d6d6d9;
    --rule-grey: #d3d3d6;
    --vine-purple: #6e3a79;
    --barcode-bg: #ffffff;
    --barcode-edge: #2a2a2a;
  }
  * { box-sizing: border-box; margin: 0; padding: 0; }
  html, body { width: 1200px; height: 797px; overflow: hidden; background: var(--page); }
  body { position: relative; font-family: "Open Sans", Arial, sans-serif; font-weight: 700; }

  .label {
    position: absolute;
    background: var(--frame);
    border: 2px solid var(--frame-edge);
  }
  .label--front { left: 65px; top: 79px; width: 428px; height: 640px; }
  .label--back  { left: 693px; top: 81px; width: 427px; height: 638px; }

  .label__field {
    position: absolute;
    background: var(--wine-red);
    overflow: hidden;
  }
  .label--front .label__field {
    left: 16px; top: 16px; width: 395px; height: 600px;
    background: radial-gradient(ellipse 60% 50% at 50% 52%, var(--wine-red-light) 0%, var(--wine-red-mid) 55%, var(--wine-red) 100%);
  }
  .label--back .label__field {
    left: 16px; top: 14px; width: 395px; height: 600px;
  }
  .texture { position: absolute; inset: 0; }

  .rule { position: absolute; height: 5px; background: var(--rule-grey); }

  /* Front label */
  .brand__mark {
    position: absolute; left: 46px; top: 13px;
    width: 34px; height: 34px; border-radius: 50%;
    background: var(--vine-purple);
  }
  .brand__line {
    position: absolute; color: var(--ink-grey);
    font-size: 20px; line-height: 24px; letter-spacing: 0.2px; white-space: nowrap;
  }
  .brand__line--name { left: 98px; top: 31px; }
  .brand__line--sub  { left: 0; right: 0; top: 63px; text-align: center; }
  .rule--brand-left  { left: 0; width: 104px; top: 72px; }
  .rule--brand-right { left: 294px; width: 101px; top: 72px; }

  .vine-art {
    position: absolute; left: 39px; top: 197px; width: 316px; height: 225px; border-radius: 50%;
    background: radial-gradient(ellipse at 50% 50%, rgba(226,200,210,0.35) 0%, rgba(110,58,121,0.25) 60%, rgba(110,58,121,0) 100%);
  }

  .front-line {
    position: absolute; left: 0; right: 0;
    text-align: center; color: var(--ink-grey); white-space: nowrap;
  }
  .region  { top: 460px; font-size: 23px; line-height: 28px; }
  .vintage { top: 496px; font-size: 30px; line-height: 36px; }
  .variety { top: 544px; font-size: 23px; line-height: 28px; }
  .rule--year-left  { left: 21px; width: 120px; top: 512px; }
  .rule--year-right { left: 253px; width: 121px; top: 512px; }

  /* Back label */
  .back-title {
    position: absolute; left: 0; right: 0; top: 29px;
    text-align: center; color: var(--ink-grey); font-size: 16px; line-height: 20px; font-weight: 700;
  }
  .story {
    position: absolute; left: 64px; width: 266px; top: 69px;
    text-align: center; color: var(--ink-white); font-size: 12.5px; line-height: 18px;
  }
  .story p { margin-bottom: 4px; }
  .story .initial { color: var(--ink-grey); font-size: 17px; font-weight: 800; }

  .drinks {
    position: absolute; left: 0; right: 0; top: 416px;
    text-align: center; color: var(--ink-grey); font-size: 16px; line-height: 20px;
  }
  .mandatories {
    position: absolute; left: 8px; top: 440px;
    color: var(--ink-white); font-size: 12px; line-height: 18px;
    list-style: none; white-space: nowrap;
  }
  .mandatories .producer { color: var(--ink-grey); font-size: 15px; line-height: 22px; }

  .barcode-space {
    position: absolute; left: 252px; top: 484px; width: 126px; height: 99px;
    background: var(--barcode-bg); border: 1px solid var(--barcode-edge);
  }
</style>
</head>
<body>

<section class="label label--front" aria-label="Front label">
  <div class="label__field">
    <div class="texture" role="img" aria-label="Red stone mosaic texture"></div>

    <span class="brand__mark" aria-hidden="true"></span>
    <p class="brand__line brand__line--name">HOLLOW CREEK</p>
    <p class="brand__line brand__line--sub">VINEYARDS</p>
    <div class="rule rule--brand-left"></div>
    <div class="rule rule--brand-right"></div>

    <div class="vine-art" role="img" aria-label="Illustration of a curling grape vine with purple leaves and a bunch of dark grapes"></div>

    <p class="front-line region">Barossa Valley</p>
    <div class="rule rule--year-left"></div>
    <p class="front-line vintage">2012</p>
    <div class="rule rule--year-right"></div>
    <p class="front-line variety">Bourdeaux</p>
  </div>
</section>

<section class="label label--back" aria-label="Back label">
  <div class="label__field">
    <div class="texture" role="img" aria-label="Red stone mosaic texture"></div>

    <h2 class="back-title">Bordeaux * 2012 * Barossa Valley</h2>

    <div class="story">
      <p><span class="initial">O</span>ur wines are planted on areas which are characterized by enormous quantities of shattered shale, slate, and limestone based rock.</p>
      <p><span class="initial">T</span>he shattered shale and limestone based rocks give name to our premium line. They are present throughout the vineyards and are a major component of the unique nature of the differing terroirs and contribute to the wines with tight structure and minerality yet abundant and generous fruit.</p>
      <p><span class="initial">O</span>ur wines drink well from release. Reds from 2 to 3 years from vintage. Cellaring potential varies between vintages but as a general rule they drink best in the range of 6 to 12 years of age</p>
    </div>

    <p class="drinks">Contains approx. 8.3 Standard Drinks</p>

    <ul class="mandatories">
      <li>750mL</li>
      <li>Wine Of Australia</li>
      <li>13.5% ALC/VOL</li>
      <li>CONTAINS SULFATES</li>
      <li>PRODUCED WITH MILK PRODUCTS</li>
      <li class="producer">Hollow Creek Vineyards</li>
      <li>Lot 7 Ferncliff Road, Eastvale, SA</li>
      <li>5399 Australia</li>
    </ul>

    <div class="barcode-space" aria-label="Space reserved for barcode"></div>
  </div>
</section>

</body>
</html>
```